Velorum Kinetics Business Card Contest

Velorum Kinetics is a b-b blockchain technology solutions company. We are seeking a professional yet minimalist business card to be designed. We would like the business card:1) to have a QR code to our website (velorum-k.example) somewhere on the card2) Colour/design to be somewhat relevant to our website (refer to attached image)3) Elegant-looking 4) No irrelevant iconsYou should use these information:Name: Eric BarbierDesignation: CEOPhone: +65 9752 2604Email: eric@triple-a.ioAddress: Singapore | China

```html
<!DOCTYPE html>
<html lang="en">
<head>
<meta charset="utf-8">
<title>Velorum Kinetics – Business Card</title>
<link href="https://fonts.googleapis.com/css2?family=Mulish:wght@400;600;800&display=swap" rel="stylesheet">
<style>
  :root {
    --backdrop: #141414;
    --card: #232323;
    --card-edge: #2c2c2c;
    --ink: #f4f4f4;
    --ink-soft: #d9d9d9;
    --accent: #1f5fae;
  }
  * { margin: 0; padding: 0; box-sizing: border-box; }
  html, body {
    width: 1200px; height: 900px; overflow: hidden;
    background: var(--backdrop);
    font-family: 'Mulish', Arial, sans-serif;
  }
  .stage {
    position: relative; width: 1200px; height: 900px;
    display: flex; flex-direction: column; align-items: center; justify-content: center; gap: 44px;
  }
  .card {
    position: relative; width: 560px; height: 320px;
    background: linear-gradient(135deg, var(--card) 0%, var(--card-edge) 100%);
    box-shadow: 0 10px 30px rgba(0,0,0,.55);
  }
  .wordmark {
    display: flex; align-items: center; gap: 12px;
    color: var(--ink); font-weight: 600; font-size: 34px; letter-spacing: 3px;
    text-transform: uppercase; white-space: nowrap;
  }
  .wordmark-dot { width: 14px; height: 14px; border-radius: 50%; background: var(--ink); }
  .card-front .wordmark {
    position: absolute; left: 50%; top: 50%; transform: translate(-50%, -50%);
  }
  .card-back .wordmark {
    position: absolute; left: 34px; top: 128px; font-size: 26px; letter-spacing: 2px; gap: 10px;
  }
  .card-back .wordmark-dot { width: 11px; height: 11px; }
  .divider {
    position: absolute; left: 318px; top: 96px; width: 2px; height: 132px; background: var(--accent);
  }
  .contact {
    position: absolute; left: 340px; top: 98px; color: var(--ink-soft);
  }
  .contact-name {
    color: var(--accent); font-weight: 800; font-size: 18px; letter-spacing: .5px; text-transform: uppercase;
  }
  .contact-role { font-size: 13px; margin-top: 2px; letter-spacing: 1px; }
  .contact-location { font-size: 14px; margin-top: 10px; letter-spacing: .5px; }
  .contact-list { list-style: none; margin-top: 8px; }
  .contact-list li {
    display: flex; align-items: center; gap: 8px; font-size: 13.5px; line-height: 21px; letter-spacing: .4px;
  }
  .contact-list svg { width: 10px; height: 10px; flex: none; }
</style>
</head>
<body>
<main class="stage">
  <section class="card card-front" aria-label="Card front">
    <div class="wordmark"><span>Velorum Kinetics</span><span class="wordmark-dot"></span></div>
  </section>

  <section class="card card-back" aria-label="Card back">
    <div class="wordmark"><span>Velorum Kinetics</span><span class="wordmark-dot"></span></div>
    <div class="divider"></div>
    <div class="contact">
      <p class="contact-name">Daniel Osgood</p>
      <p class="contact-role">CEO</p>
      <p class="contact-location">Singapore | China</p>
      <ul class="contact-list">
        <li>
          <svg viewBox="0 0 10 10" fill="none" stroke="#1f5fae" stroke-width="1.2"><path d="M2 1 L4 1 L4.6 3 L3.4 3.8 Q4.5 6 6.2 6.6 L7 5.4 L9 6 L9 8 Q5 9 1.6 4.5 Q1 2.5 2 1 Z"/></svg>
          <span>+65 8316 4079</span>
        </li>
        <li>
          <svg viewBox="0 0 10 10" fill="none" stroke="#1f5fae" stroke-width="1.2"><rect x="1" y="2" width="8" height="6"/><path d="M1 2 L5 5.5 L9 2"/></svg>
          <span>daniel@velorum-k.example</span>
        </li>
        <li>
          <svg viewBox="0 0 10 10" fill="none" stroke="#1f5fae" stroke-width="1"><circle cx="5" cy="5" r="4"/><ellipse cx="5" cy="5" rx="1.8" ry="4"/><path d="M1 5 H9"/></svg>
          <span>www.velorum-k.example</span>
        </li>
      </ul>
    </div>
  </section>
</main>
</body>
</html>
```